New B2C website design to help dads be better dads

DadHarbor is a website to help dads be the “best dad you can be.”

We require our website to be designed into a PSD format, no coding necessary.

The general concept is a two-page design. The first page is the login page, the second page is the home page. Once at the home page, rather than navigating to and from different pages, the user will push and pull through different visual and functional layers of the hierarchy. In theory, this should add to the user experience by having a visual anchor of where they are (through layered pagination) as well as improving loading times since the new information should only be a delta in data load versus a brand new page load.

The general look-and-feel we are going for is clean, simple, minimal. This means that the winning design will show us a good eye for web-optimized typography, good use of white (negative) space, and good use of a visually pleasing grid.

We require a total of 6 page "views" plus the landing page. We note that many of the views are similar to one another.
Landing page
Milestone view
Task view
Content view, articles
Content view, products
Search view
What's new view

Please review all of the additional information provided as well as the attachments for examples.

We provide the following websites as good references for:

Typography:
http://example-kelvorn.com/journal/

Use of white space:
http://www.trenvaskit.com/
http://moldrefin.com/

Example for “scrolling” page concept as well as good balance of color, typography, and white space:
http://www.qorbitalmeet.eu/

Please contact us with questions so that we can guide your design effort.
Updates

Hello designers,

The following information is added to help guide the design process:

1.  For the text dialogue below the landing page, please assume the following word count:
"why are we making dad harbor?": 250 words
"who are we?" 200 words
"what's the deal with the penguin logo?" 300 words

For the social media links, please see http://www.gravelplumbs.com/
Notice the floating "social" bar that is always to the right.  This is the concept we are going for, please try to implement this as you see fit. 

Target Market(s)

Fathers of young children ages 0-6 years old.

Industry/Entity Type

Product

Font styles to use
Sans Serif

Requirements
Must have
• Clean lines, minimal design concept

Incorporation of our logo (see attached document)

Header content is static for all views after landing page, see example

This page WILL be responsive, please keep that in mind when designing
The timeline bar should be to the left, with the timeline bar’s “milestones” also being responsive.

Designer is free to suggest font types, but any fonts used must be royalty-free and web-optimized. We request a minimum number of font types as well as fonts that load relatively fast. We reinforce that visually appealing typography is a significant factor in the winning design choice.

While we are not expecting the winning design to include code, please keep in mind that the final implementation needs to be optimized for desktop, tablet, and mobile platforms.

If you are using stock photography that is not generated by you, please provide where/how we can obtain imagery, as well as price.

All custom graphics must be available in original formats; Photoshop/GIMP layered files for layout design, and vector formats for logos, icons and other graphical elements.

Please incorporate “Blue” into design elements as you see fit, as the RGB 67 74 169 Blue is the primary color used in our brand. The complement to this blue is 255 202 0, a brownish orange. Feel free to use this color as well, although please keep it to a lesser amount.

Background color is your choice, do not feel the need to use the grey.
Should not have
• Excessive graphical content such that it affects loading times

Excessive use of too many font types such that it affects loading times

```html
<!DOCTYPE html>
<html lang="en">
<head>
<meta charset="utf-8">
<title>DadHarbor – Prepare for the baby arrival</title>
<link rel="stylesheet" href="https://fonts.googleapis.com/css2?family=Francois+One&family=Lato:wght@400&family=Open+Sans:wght@400;600;700&family=Poiret+One&family=Raleway:wght@400&family=Signika:wght@300;400&display=swap">
<style>
  :root {
    --navy: #1c2b6e;
    --brand-blue: #434aa9;
    --amber: #f2a80c;
    --ink: #111111;
    --text: #2b2b2b;
    --muted: #555555;
    --line: #d9d9d9;
    --paper: #ffffff;
    --header-top: #f0f0f0;
  }
  * { box-sizing: border-box; margin: 0; padding: 0; }
  html, body { width: 1200px; height: 918px; overflow: hidden; background: var(--paper); }
  body { position: relative; font-family: "Open Sans", sans-serif; color: var(--text); }

  .site-header {
    position: absolute; left: 0; top: 0; width: 1200px; height: 143px;
    background: linear-gradient(to bottom, var(--header-top), var(--paper));
    border-bottom: 5px solid var(--navy);
  }
  .brand {
    position: absolute; left: 30px; top: 48px; display: flex; align-items: center; gap: 8px;
    font-family: "Open Sans", sans-serif; font-weight: 700; font-size: 18px; color: var(--navy);
  }
  .brand-dot { width: 20px; height: 20px; border-radius: 50%; background: var(--navy); }
  .welcome {
    position: absolute; left: 192px; top: 12px;
    font-family: "Francois One", sans-serif; font-weight: 400; font-size: 38px; color: var(--ink);
    letter-spacing: 0.3px;
  }
  .score { position: absolute; left: 193px; top: 87px; font-size: 16px; color: var(--ink); }
  .score strong { color: var(--navy); font-weight: 700; }
  .search { position: absolute; left: 438px; top: 77px; display: flex; gap: 10px; }
  .search-field {
    width: 300px; height: 43px; border: 1px solid #cfcfcf; border-radius: 4px; background: var(--paper);
  }
  .btn {
    height: 43px; border-radius: 3px; background: var(--navy); color: #fff;
    font-family: "Open Sans", sans-serif; font-weight: 700; font-size: 16px;
    display: flex; align-items: center; justify-content: center; letter-spacing: 0.3px;
  }
  .btn-search { width: 114px; }
  .account-nav { position: absolute; left: 959px; top: 77px; display: flex; align-items: center; gap: 18px; }
  .account-link { font-size: 16px; color: var(--ink); }
  .btn-logout { width: 114px; }

  .section-band {
    position: absolute; left: 0; top: 143px; width: 1200px; height: 47px; background: var(--amber);
  }
  .section-band h2 {
    position: absolute; left: 56px; top: 7px;
    font-family: "Signika", sans-serif; font-weight: 400; font-size: 25px; color: var(--ink);
  }
  .band-pointer { position: absolute; left: 72px; top: 189px; }

  .intro {
    position: absolute; left: 56px; top: 228px; width: 940px;
    font-family: "Signika", sans-serif; font-weight: 300; font-size: 25px; line-height: 33px; color: var(--ink);
  }

  .checklist {
    position: absolute; left: 56px; top: 325px; width: 265px; height: 291px;
    border: 2px solid #e2e2e2; border-radius: 7px; list-style: none; padding: 19px 0 0 20px;
  }
  .task {
    display: flex; align-items: center; height: 32.8px;
    font-family: "Lato", sans-serif; font-size: 17px; color: var(--text);
  }
  .task-box {
    width: 19px; height: 19px; margin-right: 15px; border-radius: 4px;
    background: linear-gradient(#f4f4f4, #e3e3e3); border: 1px solid #d4d4d4;
  }
  .task-box.is-done { background: linear-gradient(#cfe3f7, #9cc4ea); border-color: #6c9fd1; }

  .site-footer { position: absolute; left: 0; top: 710px; width: 1200px; text-align: center; }
  .footer-kicker {
    font-family: "Open Sans", sans-serif; font-weight: 700; font-size: 15px;
    letter-spacing: 3px; color: var(--muted);
  }
  .footer-title {
    margin-top: 14px; font-family: "Poiret One", sans-serif; font-size: 44px; color: var(--ink);
    letter-spacing: -0.5px;
  }
  .footer-email {
    margin-top: 12px; font-family: "Open Sans", sans-serif; font-weight: 700; font-size: 20px; color: var(--brand-blue);
  }
  .footer-links {
    margin-top: 20px; font-family: "Raleway", sans-serif; font-size: 14px; color: var(--muted);
  }
  .footer-links span { margin: 0 6px; }
</style>
</head>
<body>
  <header class="site-header">
    <div class="brand"><span class="brand-dot"></span>DadHarbor</div>
    <h1 class="welcome">Welcome Greg, what would you like to do today?</h1>
    <p class="score">Super Dad Score: <strong>10,500</strong></p>
    <div class="search">
      <div class="search-field"></div>
      <div class="btn btn-search">SEARCH</div>
    </div>
    <nav class="account-nav">
      <span class="account-link">My account</span>
      <div class="btn btn-logout">LOGOUT</div>
    </nav>
  </header>

  <div class="section-band"><h2>Prepare for the baby arrival</h2></div>
  <svg class="band-pointer" width="44" height="23" viewBox="0 0 44 23" aria-hidden="true">
    <polygon points="0,0 44,0 22,22" fill="#f2a80c"/>
  </svg>

  <p class="intro">Your big day is almost here! Do you have your go-back packed? Do you have your routes (plural!) to the hospital mapped out? Lots to do, not much time!</p>

  <ul class="checklist">
    <li class="task"><span class="task-box"></span>Buy a crib</li>
    <li class="task"><span class="task-box"></span>As semble the crib</li>
    <li class="task"><span class="task-box"></span>Buy a stroller</li>
    <li class="task"><svg class="task-box is-done" viewBox="0 0 19 19" aria-hidden="true"><path d="M5 10 l3 3 l6 -8" fill="none" stroke="#0d1f3a" stroke-width="2.2" stroke-linecap="round" stroke-linejoin="round"/></svg>Buy a carseat</li>
    <li class="task"><span class="task-box"></span>Install a carseat</li>
    <li class="task"><span class="task-box"></span>Learn to change a diaper</li>
    <li class="task"><span class="task-box"></span>Learn to hold a baby</li>
    <li class="task"><span class="task-box"></span>Set a feeding schedule</li>
  </ul>

  <footer class="site-footer">
    <p class="footer-kicker">CONTACT</p>
    <p class="footer-title">GET IN TOUCH</p>
    <p class="footer-email">info@dadharbor.com</p>
    <p class="footer-links">Privacy Policy<span>|</span>© 2013 DadHarbor<span>|</span>Terms Policy<span>|</span>Disclaimer</p>
  </footer>
</body>
</html>
```